BrindleStaffing Business Card Design

We are a staffing company finding positions for dedicated nurses and physicians.

Target Market(s)

Business Professionals

Industry/Entity Type

Staffing

Contact Information for Business Card

Gordon Pratley
Chairman
417 39th Avenue South
SAINT PETERSBURG FL 33712
813-555-4172 Mobile
813-555-8036 Fax
gpratley@brindlestaffing.com
www.brindlestaffing.com

Font styles to use
Sans Serif

Colors
fbee3e
f04a50
f37122

Requirements
Must have
• Logo Attached, see colors below. We'd like to see Yellow, Orange and Red.

```html
<!DOCTYPE html>
<html lang="en">
<head>
<meta charset="utf-8">
<title>BrindleStaffing Business Card</title>
<link href="https://fonts.googleapis.com/css2?family=Open+Sans:wght@400;600;700&display=swap" rel="stylesheet">
<style>
  :root {
    --backdrop: #3a3a3a;
    --card: #141414;
    --card-edge: #1d1d1d;
    --yellow: #fbee3e;
    --orange: #f37122;
    --red: #f04a50;
    --dot-1: #fbee3e;
    --dot-2: #f8c835;
    --dot-3: #f5a02c;
    --dot-4: #f37122;
    --dot-5: #f15e3a;
    --dot-6: #f04a50;
    --text: #f2f2f2;
    --muted: #bdbdbd;
  }
  * { box-sizing: border-box; margin: 0; padding: 0; }
  html, body { width: 1200px; height: 717px; overflow: hidden; }
  body {
    background: var(--backdrop);
    font-family: "Open Sans", sans-serif;
    position: relative;
  }
  .card {
    position: absolute;
    width: 540px;
    height: 308px;
    background: linear-gradient(160deg, var(--card-edge), var(--card) 60%);
    box-shadow: 0 10px 30px rgba(0,0,0,.45);
  }
  .card--front { left: 40px; top: 70px; }
  .card--back { left: 620px; top: 330px; }

  .wordmark {
    position: absolute;
    font-weight: 700;
    font-size: 38px;
    color: var(--yellow);
    letter-spacing: -0.5px;
    white-space: nowrap;
  }
  .card--front .wordmark { left: 150px; top: 40px; }
  .card--back .wordmark { left: 150px; top: 44px; }

  .dot-row {
    position: absolute;
    left: 40px;
    top: 165px;
    width: 470px;
    display: flex;
    justify-content: space-between;
    align-items: center;
  }
  .dot { border-radius: 50%; }
  .dot:nth-child(1) { width: 42px; height: 34px; background: var(--dot-1); }
  .dot:nth-child(2) { width: 40px; height: 32px; background: var(--dot-2); }
  .dot:nth-child(3) { width: 38px; height: 30px; background: var(--dot-3); }
  .dot:nth-child(4) { width: 36px; height: 29px; background: var(--dot-4); }
  .dot:nth-child(5) { width: 36px; height: 28px; background: var(--dot-5); }
  .dot:nth-child(6) { width: 32px; height: 26px; background: var(--dot-6); }

  .person-name {
    position: absolute;
    left: 200px;
    top: 100px;
    font-size: 21px;
    font-weight: 400;
    color: var(--orange);
    letter-spacing: 0.5px;
  }
  .person-title {
    position: absolute;
    left: 201px;
    top: 130px;
    font-size: 13px;
    font-weight: 600;
    color: var(--red);
    letter-spacing: 1.5px;
    text-transform: uppercase;
  }
  .contact {
    position: absolute;
    top: 186px;
    font-size: 13px;
    color: var(--text);
    line-height: 1.35;
  }
  .contact--left { left: 28px; }
  .contact--right { left: 300px; top: 200px; }
  .contact-line { display: flex; align-items: flex-start; gap: 8px; margin-bottom: 5px; white-space: nowrap; }
  .contact-label { color: var(--muted); font-size: 11px; margin-left: 2px; line-height: 1.6; }
  .icon { flex: 0 0 13px; width: 13px; height: 13px; margin-top: 3px; }
  .divider {
    position: absolute;
    left: 272px;
    top: 188px;
    width: 2px;
    height: 72px;
    background: var(--red);
  }
</style>
</head>
<body>

<section class="card card--front" aria-label="Card front">
  <div class="wordmark">BrindleStaffing</div>
  <div class="dot-row">
    <span class="dot"></span><span class="dot"></span><span class="dot"></span>
    <span class="dot"></span><span class="dot"></span><span class="dot"></span>
  </div>
</section>

<section class="card card--back" aria-label="Card back">
  <div class="wordmark">BrindleStaffing</div>
  <div class="person-name">Gordon Pratley</div>
  <div class="person-title">Chairman</div>

  <div class="contact contact--left">
    <div class="contact-line">
      <svg class="icon" viewBox="0 0 13 13" aria-hidden="true"><rect width="13" height="13" rx="2" fill="#f37122"/><path d="M4 3 L5.5 3 L6 5 L5 5.8 Q6 7.6 7.4 8.2 L8.2 7.2 L10 7.7 L10 9.3 Q6.5 9.8 4.5 7.2 Q3.2 5.3 4 3 Z" fill="#141414"/></svg>
      <span>813-555-4172 <span class="contact-label">Mobile</span></span>
    </div>
    <div class="contact-line">
      <svg class="icon" viewBox="0 0 13 13" aria-hidden="true"><rect width="13" height="13" rx="2" fill="#f37122"/><rect x="4" y="2.5" width="5" height="3" fill="none" stroke="#141414" stroke-width="1"/><rect x="2.5" y="5.5" width="8" height="3.5" fill="#141414"/><rect x="4" y="8" width="5" height="2.7" fill="#f37122" stroke="#141414" stroke-width="1"/></svg>
      <span>813-555-8036 <span class="contact-label">Fax</span></span>
    </div>
    <div class="contact-line">
      <svg class="icon" viewBox="0 0 13 13" aria-hidden="true"><rect width="13" height="13" rx="2" fill="#f37122"/><rect x="2.5" y="4" width="8" height="5.5" fill="none" stroke="#141414" stroke-width="1.2"/><path d="M2.5 4 L6.5 7 L10.5 4" fill="none" stroke="#141414" stroke-width="1.2"/></svg>
      <span>gpratley@brindlestaffing.com</span>
    </div>
  </div>

  <div class="divider"></div>

  <div class="contact contact--right">
    <div class="contact-line">
      <svg class="icon" viewBox="0 0 13 13" aria-hidden="true"><rect width="13" height="13" rx="2" fill="#f37122"/><circle cx="6.5" cy="6.5" r="3.6" fill="none" stroke="#141414" stroke-width="1.1"/><path d="M2.9 6.5 H10.1 M6.5 2.9 Q4.6 6.5 6.5 10.1 M6.5 2.9 Q8.4 6.5 6.5 10.1" fill="none" stroke="#141414" stroke-width="0.9"/></svg>
      <span>www.brindlestaffing.com</span>
    </div>
    <div class="contact-line">
      <svg class="icon" viewBox="0 0 13 13" aria-hidden="true"><rect width="13" height="13" rx="2" fill="#f37122"/><path d="M6.5 11 Q3.2 7.4 3.2 5.4 A3.3 3.3 0 0 1 9.8 5.4 Q9.8 7.4 6.5 11 Z" fill="#141414"/><circle cx="6.5" cy="5.3" r="1.2" fill="#f37122"/></svg>
      <span>417 39th Avenue South<br>SAINT PETERSBURG FL 33712</span>
    </div>
  </div>
</section>

</body>
</html>
```